Parcelwise HQ letterhead and envelope

Design a formal (8.5x11) letterhead and envelope for sales outreach and legal matters. Using design input from https://www.parcelwisehq.example/ and the attached documents.

Industry/Entity Type

Software Service

Requirements
Must have
• These 4 hex colors are our official colors:
• #355c98 [blue]
• #1eb1a2 [teal]
• #fdba12 [gold]
• #f1653b [orange]
• So no other colors besides these should be used.

```html
<!DOCTYPE html>
<html lang="en">
<head>
<meta charset="utf-8">
<title>Parcelwise HQ Letterhead</title>
<link href="https://fonts.googleapis.com/css2?family=Lato:wght@400;700&family=Arimo:wght@400&family=Dancing+Script:wght@700&display=swap" rel="stylesheet">
<style>
  :root {
    --brand-blue: #355c98;
    --backdrop: #d6d6d6;
    --page-top: #ffffff;
    --page-bottom: #eeeeee;
    --page-border: #9a9a9a;
    --body-text: #454545;
    --heading-text: #1e1e1e;
    --meta-text: #333333;
    --divider: #c8c8c8;
  }
  * { margin: 0; padding: 0; box-sizing: border-box; }
  html, body { width: 989px; height: 1200px; overflow: hidden; background: var(--backdrop); }
  .canvas { position: relative; width: 989px; height: 1200px; }
  .letterhead {
    position: absolute; left: 69px; top: 58px; width: 839px; height: 1086px;
    background: linear-gradient(160deg, var(--page-top) 45%, var(--page-bottom) 100%);
    border: 1px solid var(--page-border);
  }
  .brand {
    position: absolute; left: 71px; top: 38px; display: flex; align-items: center; gap: 12px;
    font-family: "Lato", sans-serif; font-weight: 400; font-size: 38px; color: var(--brand-blue);
    letter-spacing: 0.2px;
  }
  .brand-dot { width: 44px; height: 44px; border-radius: 50%; border: 5px solid var(--brand-blue); }
  .contact {
    position: absolute; left: 622px; top: 24px; padding-left: 11px; border-left: 1px solid var(--divider);
    font-family: "Arimo", sans-serif; font-size: 13px; color: var(--meta-text); list-style: none;
  }
  .contact li { display: flex; align-items: center; gap: 5px; height: 22px; }
  .contact svg { width: 12px; height: 12px; flex: none; }
  .salutation {
    position: absolute; left: 71px; top: 280px;
    font-family: "Lato", sans-serif; font-weight: 700; font-size: 15.5px; color: var(--brand-blue);
  }
  .body-copy { position: absolute; left: 71px; top: 315px; width: 697px; }
  .body-copy p {
    font-family: "Lato", sans-serif; font-size: 15.5px; line-height: 24.9px; color: var(--body-text);
    text-align: justify; margin-bottom: 17px;
  }
  .closing {
    position: absolute; left: 71px; top: 757px;
    font-family: "Lato", sans-serif; font-size: 18px; color: var(--heading-text);
  }
  .signature {
    position: absolute; left: 71px; top: 784px;
    font-family: "Dancing Script", cursive; font-weight: 700; font-size: 32px; color: var(--brand-blue);
  }
  .address {
    position: absolute; left: 0; right: 0; top: 1054px; display: flex; justify-content: center; align-items: center; gap: 5px;
    font-family: "Arimo", sans-serif; font-size: 12.5px; color: var(--meta-text);
  }
  .address svg { width: 11px; height: 12px; }
</style>
</head>
<body>
<div class="canvas">
  <section class="letterhead">
    <div class="brand"><span class="brand-dot"></span><span class="brand-name">Parcelwise HQ</span></div>

    <ul class="contact">
      <li><svg viewBox="0 0 12 12"><circle cx="6" cy="6" r="5.3" fill="none" stroke="#355c98" stroke-width="1.2"/><rect x="4" y="3" width="4" height="6" rx="0.8" fill="none" stroke="#355c98" stroke-width="1"/></svg>(555) 014-2288</li>
      <li><svg viewBox="0 0 12 12"><circle cx="6" cy="6" r="5.3" fill="none" stroke="#355c98" stroke-width="1.2"/><path d="M4 3.2 L5 3 L5.6 4.6 L4.9 5.2 Q5.5 6.6 6.8 7.2 L7.4 6.5 L9 7.1 L8.8 8.1 Q6.2 8.6 4 5.6 Z" fill="#355c98"/></svg>(555) 019-3073(Main)</li>
      <li><svg viewBox="0 0 12 12"><circle cx="6" cy="6" r="5.3" fill="none" stroke="#355c98" stroke-width="1.2"/><rect x="3.3" y="4.2" width="5.4" height="3.8" fill="none" stroke="#355c98" stroke-width="1"/><path d="M3.3 4.2 L6 6.4 L8.7 4.2" fill="none" stroke="#355c98" stroke-width="1"/></svg>jsmith@parcelwisehq.example</li>
      <li><svg viewBox="0 0 12 12"><circle cx="6" cy="6" r="5.3" fill="none" stroke="#355c98" stroke-width="1.2"/><ellipse cx="6" cy="6" rx="2.2" ry="5.3" fill="none" stroke="#355c98" stroke-width="0.9"/><path d="M0.8 6 H11.2 M1.8 3.5 H10.2 M1.8 8.5 H10.2" stroke="#355c98" stroke-width="0.9"/></svg>www.parcelwisehq.example</li>
    </ul>

    <h1 class="salutation">Dear Mr. Lorem,</h1>

    <div class="body-copy">
      <p>Lorem ipsum dolor sit amet, consectetuer adipiscing elit, sed diam nonummy nibh euismod tincidunt ut laoreet dolore magna aliquam erat volutpat. Ut wisi enim ad minim veniam, quis nostrud exerci tation ullamcorper suscipit lobortis nisl ut aliquip ex ea commodo consequat. Duis autem vel eum iriure dolor in hendiusto odio dignissim qui blandit praesent luptatum zzril delenit augue duis dolore te feugait nulla facilisi.</p>
      <p>Lorem ipsum dolor sit amet, consectetuer adipiscing elit, sed diam nonummy nibh euismod tincidunt ut laoreet dolore magna aliquam erat volutpat. Ut wisi enim ad minim veniam, quis nostrud exerci tation ullamcorper suscipit lobortis nisl ut aliquip ex ea commodo consequat. Duis autem vel eum iriure dolor in hendiusto odio dignissim qui blandit praesent luptatum zzril delenit augue duis dolore te feugait nulla facilisi.</p>
      <p>Lorem ipsum dolor sit amet, consectetuer adipiscing elit, sed diam nonummy nibh euismod tincidunt ut laoreet dolore magna aliquam erat volutpat. Ut wisi enim ad minim veniam, quis nostrud exerci tation ullamcorper suscipit lobortis nisl ut aliquip ex ea commodo consequat. Duis autem vel eum iriure dolor in hendiusto odio dignissim qui blandit praesent luptatum zzril delenit augue duis dolore te feugait nulla facilisi.</p>
    </div>

    <p class="closing">Sincerely Your,</p>
    <p class="signature">Your Name</p>

    <p class="address"><svg viewBox="0 0 11 12"><path d="M5.5 11.3 C2.5 7.8 1.2 6 1.2 4.4 A4.3 4.3 0 0 1 9.8 4.4 C9.8 6 8.5 7.8 5.5 11.3 Z" fill="none" stroke="#355c98" stroke-width="1.1"/><circle cx="5.5" cy="4.5" r="1.5" fill="#355c98"/></svg>27 Quarry Lane, Fairhaven, MI 40000</p>
  </section>
</div>
</body>
</html>
```